Marwick Law Letterhead

We need a new letterhead design for a Law Firm. The address for the law firm is 1475 Calloway Street, Suite 210, Houston, Texas 77041. Phone Number: 832-361-9027; Fax Number: 832-614-7359. The logo is uploaded to the project.

```html
<!DOCTYPE html>
<html lang="en">
<head>
<meta charset="UTF-8">
<title>Marwick Law Letterhead</title>
<link href="https://fonts.googleapis.com/css2?family=Montserrat:wght@400;500;600&display=swap" rel="stylesheet">
<style>
  :root {
    --navy: #1c3260;
    --navy-light: #223c72;
    --red: #d91f2b;
    --red-dark: #8e1018;
    --ink: #2b2b2b;
    --paper: #ffffff;
    --backdrop: #e8e8e8;
  }
  * { margin: 0; padding: 0; box-sizing: border-box; }
  html, body {
    width: 1154px; height: 1200px; overflow: hidden;
    background: var(--backdrop);
    font-family: "Montserrat", Arial, sans-serif;
  }
  .letterhead {
    position: absolute; left: 167px; top: 27px;
    width: 820px; height: 1146px;
    background: var(--paper);
    box-shadow: 0 6px 24px rgba(0,0,0,0.18);
    overflow: hidden;
  }
  .header-shape, .footer-band { position: absolute; left: 0; }
  .header-shape { top: 0; }
  .footer-band { top: 1065px; }
  .brand {
    position: absolute; left: 32px; top: 62px;
    display: flex; align-items: center; gap: 10px;
  }
  .brand-dot { width: 16px; height: 16px; border-radius: 50%; background: var(--red); }
  .brand-name {
    font-size: 30px; font-weight: 600; color: var(--navy); letter-spacing: 0.3px;
  }
  .contact {
    position: absolute; left: 623px; top: 42px;
    color: #fff; font-size: 14px; line-height: 18px;
  }
  .contact-address { margin-bottom: 8px; }
  .contact-line { display: flex; align-items: center; gap: 10px; height: 21px; }
  .contact-line svg { width: 12px; height: 12px; }
  .recipient {
    position: absolute; left: 30px; top: 272px;
    font-size: 14px; line-height: 20.4px; color: #222;
  }
  .letter-body {
    position: absolute; left: 32px; top: 360px; width: 758px;
    font-size: 13.4px; line-height: 20.4px; color: var(--ink);
    text-align: justify;
  }
  .letter-body p { margin-bottom: 20.4px; }
  .closing {
    position: absolute; left: 30px; top: 935px;
    font-size: 16px; color: #222;
  }
  .signature {
    position: absolute; left: 28px; top: 962px; width: 92px; height: 28px;
    background: linear-gradient(90deg, #3a3a3a22, #3a3a3a55, #3a3a3a22);
    border-radius: 4px;
  }
  .website {
    position: absolute; left: 495px; top: 1080px;
    display: flex; align-items: center; gap: 7px;
    color: #fff; font-size: 14px;
  }
  .website svg { width: 13px; height: 13px; }
</style>
</head>
<body>
<main class="letterhead">
  <svg class="header-shape" width="820" height="190" viewBox="0 0 820 190" aria-hidden="true">
    <defs>
      <linearGradient id="stripeRed" x1="0" y1="0" x2="0" y2="1">
        <stop offset="0" stop-color="#e3202c"/>
        <stop offset="1" stop-color="#9b1119"/>
      </linearGradient>
    </defs>
    <polygon points="391,0 407,0 547,184 532,184" fill="url(#stripeRed)"/>
    <polygon points="407,0 820,0 820,184 547,184" fill="var(--navy)"/>
  </svg>

  <div class="brand">
    <span class="brand-dot"></span>
    <span class="brand-name">Marwick Law</span>
  </div>

  <div class="contact">
    <div class="contact-address">1475 Calloway Street,<br>Suite 210, Houston,<br>Texas 77041</div>
    <div class="contact-line">
      <svg viewBox="0 0 24 24"><path fill="#fff" d="M6.6 10.8a15.1 15.1 0 0 0 6.6 6.6l2.2-2.2a1 1 0 0 1 1-.25 11.4 11.4 0 0 0 3.6.57 1 1 0 0 1 1 1V20a1 1 0 0 1-1 1A17 17 0 0 1 3 4a1 1 0 0 1 1-1h3.5a1 1 0 0 1 1 1c0 1.25.2 2.45.57 3.6a1 1 0 0 1-.25 1z"/></svg>
      <span>832-361-9027</span>
    </div>
    <div class="contact-line">
      <svg viewBox="0 0 24 24"><path fill="#fff" d="M6 2h12v5H6zM4 8h16a2 2 0 0 1 2 2v7h-4v5H6v-5H2v-7a2 2 0 0 1 2-2zm4 8v4h8v-4z"/></svg>
      <span>832-614-7359</span>
    </div>
  </div>

  <div class="recipient">
    Mr/s<br>First Name and Last Name<br>Company Name<br>Address
  </div>

  <div class="letter-body">
    <p>Lorem ipsum dolor sit amet,consectetur adipiscing sed do eiusmod tempor incididunt laboreet dolore magna aliqua.Ut enim ad minim.veniam, quis nostrud exercitation ullamco laboris nisi ut aliquip exea commodo consequat.Lorem ipsum dolor sit amet,consectetur adipiscing sed do eiusmod tempor incididunt.labore et dolore magna aliqua. Ut enim</p>
    <p>Lorem ipsum dolor sit amet, consectetur adipiscing sed do eiusmod tempor incididunt labore et dolore magna aliqua. Ut enim ad minim veniam, quis nostrud exercitation ullamco laboris nisi ut aliquip exea commodo consequat.Duis aute irure dolor in reprehenderit in voluptate velit esse cillum irure dolor in reprehenderit in voluptate velit esse irure</p>
    <p>Lorem ipsum dolor sit amet, consectetur adipiscing sed do eiusmod tempor incididunt labore et dolore magna aliqua. consequat. Duis aute irure dolor in.reprehenderit in voluptate velit esse cillum dolore eu fugiat nulla pariatur. Excepteur sint occaecat cupidatat non proident, sunt in culpa qui officia deserunt mollit,</p>
    <p>Lorem ipsum dolor sit amet, consectetur adipiscing sed do eiusmod tempor incididunt labore et dolore magna aliqua. Ut enim Lorem ipsum dolor sit amet, consectetur adipiscing sed do eiusmod tempor incididunt labore et dolore magna aliqua. Ut enim Lorem ipsum aliqua.ipsum</p>
    <p>Lorem ipsum dolor sit amet, consectetur adipiscing sed do eiusmod tempor incididunt labore et dolore magna aliqua. Ut enim ad minim veniam, quis nostrud exercitation ullamco laboris nisi ut aliquip exea commodo consequat.Duis aute irure dolor in reprehenderit in voluptate velit esse cillum irure dolor in reprehenderit in voluptate velit esse irure</p>
    <p>Lorem ipsum dolor sit amet, consectetur adipiscing sed do eiusmod tempor incididunt labore et dolore magna aliqua. Ut enim ad minim veniam, quis nostrud exercitation ullamco laboris nisi ut aliquip exea commodo consequat.Duis aute irure dolor in reprehenderit in voluptate velit esse cillum irure dolor in reprehenderit in voluptate velit esse irure</p>
  </div>

  <div class="closing">Regards</div>
  <div class="signature" role="img" aria-label="Handwritten signature"></div>

  <svg class="footer-band" width="820" height="47" viewBox="0 0 820 47" aria-hidden="true">
    <defs>
      <linearGradient id="bandNavy" x1="0" y1="0" x2="1" y2="0">
        <stop offset="0" stop-color="#172b52"/>
        <stop offset="1" stop-color="#223c72"/>
      </linearGradient>
      <linearGradient id="bandRed" x1="0" y1="0" x2="1" y2="0">
        <stop offset="0" stop-color="#d91f2b"/>
        <stop offset="0.55" stop-color="#c81b27"/>
        <stop offset="1" stop-color="#7e0e16"/>
      </linearGradient>
    </defs>
    <polygon points="0,0 473,0 451,47 0,47" fill="url(#bandNavy)"/>
    <polygon points="485,0 684,0 654,47 462,47" fill="url(#bandRed)"/>
    <polygon points="695,0 820,0 820,47 665,47" fill="url(#bandNavy)"/>
  </svg>

  <div class="website">
    <svg viewBox="0 0 24 24"><circle cx="12" cy="12" r="10" fill="#fff"/><path fill="#c81b27" d="M8 6c2 0 3 1 2.5 2.5S8 10 9 12s-1 3-2 3-2-2-2-4 1-5 3-5zm7 8c1.5 0 2.5 1 2 2.5s-2 2.5-3 2-1-2-.5-3 1-1.5 1.5-1.5z"/></svg>
    <span>www.marwicklaw.com</span>
  </div>
</main>
</body>
</html>
```